High-end construction company needs a business card design

We need a modern looking business card that draws people in, is memorable and looks so good people will want to sick it on their fridges.
On the first side what is needed are:
Logo
My name - Tomasz Brelwik
Title - Managing Director
Website - www.varkelt.co.uk
Email - tomasz@varkelt.co.uk
Telephone - 020 5194 6281
Mobile - 07845139072
On the back side was is needed is a list of all the services we provide:
-Kitchen Renovations
-Bathroom Renovations
-House Renovations
-Garage Conversions
-Extensions
-Loft Conversions
-Conservatories
-Carpentry
-Tiling
-Electrical
-Plumbing & Heating
-Bricklaying
-Landscaping
-Decorating
-Plastering
We would like the colours to be the same shades as on the logo with grey or black for the words.
Target Market(s)
Anyone who needs building work done
Contact Information for Business Card
This business card is for a construction company which strives to deliver excellent service and quality.
The look and feel of the card should represent this.
Requirements
Must have
- On the first side what is needed are:
Logo
My name - Tomasz Brelwik
Title - Managing Director
Website - www.varkelt.co.uk
Email - tomasz@varkelt.co.uk
Telephone - 020 5194 6281
Mobile - 07845139072
Nice to have
- Cool looking features

```html
<!DOCTYPE html>
<html lang="en">
<head>
<meta charset="utf-8">
<title>Varkelt Construction Ltd – Business Card</title>
<link rel="stylesheet" href="https://fonts.googleapis.com/css2?family=Open+Sans:wght@400;700&display=swap">
<style>
  :root {
    --green: #5aa640;
    --green-light: #7cc242;
    --green-dark: #4a8f3c;
    --green-deep: #468a3a;
    --divider: #a6dd6e;
    --ink: #5b5b5b;
    --paper: #ffffff;
    --backdrop: #e9ebe8;
  }
  * { box-sizing: border-box; margin: 0; padding: 0; }
  html, body { width: 1200px; height: 1126px; overflow: hidden; }
  body {
    background: var(--backdrop);
    font-family: "Open Sans", Arial, sans-serif;
    position: relative;
  }
  .card {
    position: absolute;
    left: 190px;
    width: 820px;
    height: 496px;
    box-shadow: 0 6px 18px rgba(0,0,0,0.18);
    overflow: hidden;
  }
  /* ---------- Back side ---------- */
  .card-back {
    top: 44px;
    background: linear-gradient(160deg, var(--green) 0%, var(--green-deep) 100%);
    color: var(--paper);
    text-align: center;
  }
  .card-back .brand {
    position: absolute;
    top: 110px;
    left: 0; right: 0;
  }
  .brand-name {
    font-weight: 700;
    letter-spacing: 2px;
    text-transform: uppercase;
    line-height: 1;
  }
  .brand-name .main { display: block; font-size: 64px; }
  .brand-name .sub { display: block; font-size: 19px; letter-spacing: 6px; margin-top: 8px; }
  .services {
    position: absolute;
    top: 300px;
    left: 40px; right: 40px;
    list-style: none;
    font-size: 21px;
    line-height: 38px;
  }
  .services li { display: block; }
  .services .sep { color: var(--divider); margin: 0 8px; }

  /* ---------- Front side ---------- */
  .card-front {
    top: 586px;
    background: var(--paper);
  }
  .card-front .brand {
    position: absolute;
    top: 62px;
    left: 62px;
    color: var(--green);
  }
  .card-front .brand-name .main { font-size: 60px; }
  .card-front .brand-name .sub { font-size: 17px; letter-spacing: 5px; }
  .person {
    position: absolute;
    top: 226px;
    right: 62px;
    text-align: right;
  }
  .person-name { font-size: 30px; font-weight: 700; color: var(--green-light); line-height: 36px; }
  .person-title { font-size: 22px; line-height: 30px; color: var(--ink); }
  .rule {
    position: absolute;
    top: 308px;
    left: 62px;
    width: 696px;
    height: 2px;
    background: var(--green-light);
  }
  .contact {
    position: absolute;
    top: 326px;
    left: 62px;
    list-style: none;
    font-size: 22px;
    line-height: 32px;
    color: var(--ink);
  }
  .contact li { display: flex; align-items: center; gap: 12px; }
  .contact svg { width: 18px; height: 18px; fill: var(--green-light); flex: none; }
  .website {
    position: absolute;
    right: 62px;
    top: 392px;
    font-size: 22px;
    line-height: 30px;
    color: var(--ink);
  }
  .website .accent { color: var(--green-light); }
  .band { position: absolute; left: 0; bottom: 0; width: 820px; height: 40px; }
</style>
</head>
<body>

<section class="card card-back" aria-label="Card back – services">
  <div class="brand">
    <p class="brand-name"><span class="main">Varkelt</span><span class="sub">Construction Ltd</span></p>
  </div>
  <ul class="services">
    <li>Kitchen Renovations<span class="sep">|</span>Bathroom Renovations<span class="sep">|</span>House Renovations</li>
    <li>Garage Conversions<span class="sep">|</span>Extensions<span class="sep">|</span>Loft Conversions<span class="sep">|</span>Conservatories</li>
    <li>Carpentry<span class="sep">|</span>Tiling<span class="sep">|</span>Electrical<span class="sep">|</span>Plumbing &amp; Heating<span class="sep">|</span>Bricklaying</li>
    <li>Landscaping<span class="sep">|</span>Decorating<span class="sep">|</span>Plastering</li>
  </ul>
</section>

<section class="card card-front" aria-label="Card front – contact">
  <div class="brand">
    <p class="brand-name"><span class="main">Varkelt</span><span class="sub">Construction Ltd</span></p>
  </div>

  <div class="person">
    <p class="person-name">Tomasz Brelwik</p>
    <p class="person-title">Managing Director</p>
  </div>

  <div class="rule"></div>

  <ul class="contact">
    <li>
      <svg viewBox="0 0 24 24" aria-hidden="true"><path d="M6.6 10.8a15.1 15.1 0 0 0 6.6 6.6l2.2-2.2c.3-.3.7-.4 1-.2 1.1.4 2.3.6 3.6.6.6 0 1 .4 1 1V20c0 .6-.4 1-1 1A17 17 0 0 1 3 4c0-.6.4-1 1-1h3.5c.6 0 1 .4 1 1 0 1.3.2 2.5.6 3.6.1.3 0 .7-.2 1z"/></svg>
      020 5194 6281
    </li>
    <li>
      <svg viewBox="0 0 24 24" aria-hidden="true"><path d="M7 1h10a2 2 0 0 1 2 2v18a2 2 0 0 1-2 2H7a2 2 0 0 1-2-2V3a2 2 0 0 1 2-2zm0 3v14h10V4zm5 15.2a1.2 1.2 0 1 0 0 2.4 1.2 1.2 0 0 0 0-2.4z"/></svg>
      07845139072
    </li>
    <li>
      <svg viewBox="0 0 24 24" aria-hidden="true"><path d="M2 5h20v14H2zm2 2v.4l8 5.2 8-5.2V7zm0 2.8V17h16V9.8l-8 5.2z"/></svg>
      tomasz@varkelt.co.uk
    </li>
  </ul>

  <p class="website">www.<span class="accent">varkelt</span>.co.uk</p>

  <svg class="band" viewBox="0 0 820 40" preserveAspectRatio="none" aria-hidden="true">
    <polygon points="0,8 820,28 820,40 0,40" fill="#7cc242"/>
    <polygon points="500,24 820,14 820,40 480,40" fill="#ffffff"/>
    <polygon points="508,24 820,14 820,40 490,40" fill="#4a8f3c"/>
  </svg>
</section>

</body>
</html>
```